business card

Business card for new business.
Red and black corporate colors.
Card can have an Indsutrial feel to it. Feel free to add Rust, Bolted steel, or graphics as you see fit. We provide highly specialized services to the below mentioned industries.
Keep information out of corners so that if I want I can choose rounded corners.
Information
- front. name - title - phone - email
- Rear
Refining - Rail - Infrastructure - Mining - Energy
Calgary - Edmonton - Fort McMurray - Revelstoke - Vancouver

```html
<!DOCTYPE html>
<html lang="en">
<head>
<meta charset="utf-8">
<title>Ironvale Business Card</title>
<link href="https://fonts.googleapis.com/css2?family=Arimo:wght@400;700&display=swap" rel="stylesheet">
<style>
  :root {
    --backdrop: #161719;
    --card: #202326;
    --text-grey: #8a8d90;
    --name-grey: #a5a8ab;
    --brand-silver: #b9bcbf;
    --accent-red: #d1262b;
  }
  * { margin: 0; padding: 0; box-sizing: border-box; }
  html, body { width: 1200px; height: 800px; overflow: hidden; }
  body {
    background: var(--backdrop);
    font-family: "Arimo", Arial, sans-serif;
    position: relative;
  }
  .card {
    position: absolute;
    top: 257px;
    width: 500px;
    height: 286px;
    background: var(--card);
    box-shadow: 0 12px 30px rgba(0,0,0,0.45);
  }
  .card-front { left: 70px; }
  .card-back { left: 630px; }

  /* front: brand */
  .brand {
    position: absolute;
    left: 50%; top: 50%;
    transform: translate(-50%, -50%);
    display: flex;
    align-items: center;
    gap: 14px;
  }
  .brand-square {
    width: 22px; height: 22px;
    background: var(--brand-silver);
  }
  .brand-name {
    font-weight: 700;
    font-size: 40px;
    letter-spacing: 2px;
    color: var(--brand-silver);
  }

  /* back: contact block */
  .contact-block {
    position: absolute;
    left: 60px; top: 78px;
    display: flex;
    align-items: center;
    gap: 22px;
  }
  .person-name {
    font-weight: 700;
    font-size: 17px;
    color: var(--name-grey);
  }
  .person-title {
    font-size: 14px;
    color: var(--accent-red);
    margin-top: 2px;
  }
  .divider {
    width: 1px; height: 60px;
    background: var(--accent-red);
  }
  .contact-list { list-style: none; }
  .contact-list li {
    display: flex;
    align-items: center;
    gap: 8px;
    font-size: 12px;
    color: var(--text-grey);
    line-height: 19px;
  }
  .contact-list svg { width: 11px; height: 11px; flex: none; }

  .services {
    position: absolute;
    left: 60px; bottom: 52px;
    font-size: 12.5px;
    color: var(--text-grey);
    line-height: 19px;
  }
  .sep { color: var(--accent-red); padding: 0 3px; }
</style>
</head>
<body>

<section class="card card-front">
  <div class="brand">
    <span class="brand-square"></span>
    <span class="brand-name">IRONVALE</span>
  </div>
</section>

<section class="card card-back">
  <div class="contact-block">
    <div class="person">
      <p class="person-name">Dana Keller</p>
      <p class="person-title">Managing Director</p>
    </div>
    <span class="divider"></span>
    <ul class="contact-list">
      <li>
        <svg viewBox="0 0 12 12"><rect x="3" y="1" width="6" height="10" rx="1" fill="none" stroke="#d1262b" stroke-width="1.5"/></svg>
        (01) 555 0148
      </li>
      <li>
        <svg viewBox="0 0 12 12"><rect x="0.5" y="2" width="11" height="8" fill="#d1262b"/><path d="M0.5 2 L6 7 L11.5 2" fill="none" stroke="#202326" stroke-width="1.2"/></svg>
        info@ironvalecorp.com
      </li>
      <li>
        <svg viewBox="0 0 12 12"><circle cx="6" cy="6" r="5.3" fill="#d1262b"/><path d="M0.7 6 H11.3 M6 0.7 V11.3" stroke="#202326" stroke-width="0.9"/><ellipse cx="6" cy="6" rx="2.4" ry="5.3" fill="none" stroke="#202326" stroke-width="0.9"/></svg>
        www.ironvalecorp.com
      </li>
    </ul>
  </div>

  <div class="services">
    <p>Refining<span class="sep">|</span>Rail<span class="sep">|</span>Infrastructure<span class="sep">|</span>Mining<span class="sep">|</span>Energy</p>
    <p>Calgary<span class="sep">|</span>Edmonton<span class="sep">|</span>Fort McMurray<span class="sep">|</span>Revelstoke<span class="sep">|</span>Vancouver</p>
  </div>
</section>

</body>
</html>
```